Fresh, modern, fun business card for pediatric dental practice

Need a business card for fresh, modern, fun pediatric dental practice

Clean look that matches our website's font and colors

We prefer the look of curved corners on business cards

Target Market(s)

parents (mothers) of young children, professionals, mid-high class

Industry/Entity Type

Dental

Contact Information for Business Card

Maplebrook Pediatric Dentistry
482 Quarry Lane
Suite 517
Fernhollow, PA 17099
717.555.0193
www.maplebrookkidsdental.example

Mei-Ran Tsai, DMD
Corinne Walbeck, DMD
(we are working on our email address, but we would like that on the card as well)

Font styles to use
Sans Serif

Requirements
Must have
• All info; we would also like to make cards for individual staff members
• colors from our website and color palatte, attatched
• use same font and design as website for branding
Nice to have
• clean, simple card that has a pop of color
• we would like to see a few designs with our tag line "where smiles get brighter"
• we are not sure if we want to have it on there or not
• we would like to see a few designs incorporating the ribbon graphic on our website where the word WELCOME is

```html
<!DOCTYPE html>
<html lang="en">
<head>
<meta charset="utf-8">
<title>Maplebrook Pediatric Dentistry – Business Card</title>
<link rel="stylesheet" href="https://fonts.googleapis.com/css2?family=Open+Sans:wght@600&family=Roboto:wght@400&family=Roboto+Condensed:wght@700&display=swap">
<style>
  :root {
    --backdrop: #2a2a2a;
    --card-white: #f3f3f3;
    --sun-yellow: #eeb224;
    --berry: #c8318a;
    --ink: #444444;
    --white: #ffffff;
  }
  html, body {
    margin: 0;
    padding: 0;
    width: 1200px;
    height: 960px;
    overflow: hidden;
    background: var(--backdrop);
  }
  .canvas {
    position: relative;
    width: 1200px;
    height: 960px;
  }
  .card {
    position: absolute;
    width: 600px;
    height: 342px;
    border-radius: 22px;
    overflow: hidden;
  }
  .card--front { left: 314px; top: 113px; background: var(--card-white); }
  .card--back { left: 311px; top: 472px; background: var(--sun-yellow); }

  .brand-mark {
    position: absolute;
    left: 136px;
    top: 48px;
    width: 26px;
    height: 26px;
    border-radius: 50%;
    background: var(--sun-yellow);
  }
  .brand-name {
    position: absolute;
    left: 40px;
    top: 92px;
    margin: 0;
    font-family: "Open Sans", sans-serif;
    font-weight: 600;
    color: var(--sun-yellow);
    line-height: 1;
  }
  .brand-name .primary { display: block; font-size: 38px; letter-spacing: 0.5px; }
  .brand-name .secondary { display: block; font-size: 19px; margin-top: 6px; letter-spacing: 0.8px; }

  .name-band {
    position: absolute;
    left: 0;
    top: 187px;
    width: 600px;
    height: 60px;
    background: linear-gradient(to right, var(--sun-yellow) 0 476px, var(--berry) 476px 100%);
  }
  .practitioners {
    position: absolute;
    left: 40px;
    top: 7px;
    margin: 0;
    font-family: "Roboto Condensed", sans-serif;
    font-weight: 700;
    font-size: 20px;
    line-height: 24px;
    color: var(--white);
  }

  .address {
    position: absolute;
    left: 37px;
    top: 263px;
    margin: 0;
    font-family: "Roboto", sans-serif;
    font-style: normal;
    font-size: 14px;
    line-height: 18px;
    color: var(--ink);
  }
  .contact {
    position: absolute;
    right: 40px;
    top: 280px;
    margin: 0;
    padding: 0;
    list-style: none;
    font-family: "Roboto", sans-serif;
    font-size: 14px;
    line-height: 20px;
    color: var(--ink);
    text-align: right;
  }
  .contact li { display: flex; align-items: center; justify-content: flex-end; gap: 5px; }
  .contact svg { width: 13px; height: 13px; }

  .back-brand {
    position: absolute;
    left: 37px;
    top: 228px;
    margin: 0;
    font-family: "Open Sans", sans-serif;
    font-weight: 600;
    color: var(--white);
    line-height: 1;
  }
  .back-brand .primary { display: block; font-size: 40px; letter-spacing: 0.5px; }
  .back-brand .secondary { display: block; font-size: 21px; margin-top: 5px; letter-spacing: 1px; }
  .back-url {
    position: absolute;
    left: 37px;
    top: 300px;
    margin: 0;
    font-family: "Open Sans", sans-serif;
    font-weight: 600;
    font-size: 13px;
    letter-spacing: 1.2px;
    color: var(--white);
  }
</style>
</head>
<body>
<main class="canvas">
  <section class="card card--front" aria-label="Business card front">
    <span class="brand-mark" aria-hidden="true"></span>
    <h1 class="brand-name">
      <span class="primary">Maplebrook</span>
      <span class="secondary">Pediatric Dentistry</span>
    </h1>

    <div class="name-band">
      <p class="practitioners">Mei-Ran Tsai, DMD<br>Corinne Walbeck, DMD</p>
    </div>

    <address class="address">
      Maplebrook Pediatric Dentistry<br>
      482 Quarry Lane<br>
      Suite 517, Fernhollow, PA 17099
    </address>

    <ul class="contact">
      <li>717.555.0193
        <svg viewBox="0 0 16 16" aria-hidden="true"><path fill="#eeb224" d="M3.6 1.2l2.3 2.6-1.3 1.9c.9 2 2.6 3.7 4.6 4.6l1.9-1.3 2.6 2.3-1.4 2.6C6.4 13.6 2.4 9.6 1 3.7z"/></svg>
      </li>
      <li>maplebrookkidsdental.example
        <svg viewBox="0 0 16 16" aria-hidden="true"><circle cx="8" cy="8" r="7" fill="#eeb224"/><path d="M4 6.5c1.5-.5 2.5.5 3 1.5s-1 2-.5 3M9.5 3.5c0 1.5 1.5 1.5 2.5 2.5" stroke="#fff" stroke-width="1.3" fill="none"/></svg>
      </li>
    </ul>
  </section>

  <section class="card card--back" aria-label="Business card back">
    <h2 class="back-brand">
      <span class="primary">Maplebrook</span>
      <span class="secondary">Pediatric Dentistry</span>
    </h2>
    <p class="back-url">www.maplebrookkidsdental.example</p>
  </section>
</main>
</body>
</html>
```